Lendquay wedsite and logo refresh

We are looking for someone to refresh the look and feel of Lendquay.co.nz we are moving it towards a more traditional brokerage.

Target Market(s)

30 to 55 year old professionals

Coding

Coded - Design and coding required

Number of Pages Required

3 page

Requirements
Nice to have
• we are needing a modern professional look

```html
<!DOCTYPE html>
<html lang="en">
<head>
<meta charset="utf-8">
<title>Lendquay</title>
<link rel="stylesheet" href="https://fonts.googleapis.com/css2?family=Rajdhani:wght@500;600;700&family=Roboto:wght@400;500;700&display=swap">
<style>
:root{
  --orange:#e8431c;
  --orange-dark:#c9340f;
  --ink:#222;
  --body:#555;
  --dark:#2d2d2d;
  --light:#efefef;
  --white:#fff;
}
*{box-sizing:border-box;margin:0;padding:0}
html,body{width:1200px;height:4292px;overflow:hidden;background:var(--white)}
body{position:relative;font-family:Roboto,Arial,sans-serif;color:var(--ink)}
.abs{position:absolute}
.heading{font-family:Rajdhani,Arial,sans-serif;font-weight:700;text-transform:uppercase;letter-spacing:.3px}
.accent{color:var(--orange)}
.pill{display:flex;align-items:center;justify-content:center;border-radius:30px;font-weight:700;font-size:14px;text-transform:uppercase}

/* header */
.site-header{top:0;left:0;width:1200px;height:110px;background:var(--white)}
.logo{left:112px;top:30px;font-family:Rajdhani,sans-serif;font-weight:500;font-size:44px;color:var(--orange);letter-spacing:1px}
.call-label{left:660px;top:21px;font-size:10px;font-weight:500}
.call-number{left:660px;top:33px;font-size:22px;font-weight:700;color:var(--orange)}
.btn-login{left:837px;top:22px;width:96px;height:34px;border:2px solid var(--orange);color:var(--orange);font-size:13px;text-transform:none;font-weight:500}
.btn-signup{left:950px;top:22px;width:138px;height:34px;background:var(--orange);color:#fff;font-size:13px;text-transform:none}
.nav{top:84px;left:392px;display:flex;gap:30px;font-size:13px;font-weight:700}
.nav span{padding-bottom:8px}
.nav .active{color:var(--orange);border-bottom:3px solid var(--orange)}

/* hero */
.hero{top:110px;left:0;width:1200px;height:590px;background:linear-gradient(180deg,#2d3d66 0%,#5a5076 25%,#a06670 42%,#6b6a7a 55%,#3f4a3a 72%,#3b6b22 100%)}
.hero-title{top:162px;width:100%;text-align:center;color:#fff;font-size:43px;line-height:47px}
.hero-btn{left:467px;top:335px;width:266px;height:46px;background:var(--orange);color:#fff;font-size:14px;gap:8px}
.hero-arrow{top:275px;width:42px;height:42px;border:2px solid #fff;border-radius:50%;display:flex;align-items:center;justify-content:center}

/* welcome */
.welcome{top:700px;left:0;width:1200px;height:192px;background:linear-gradient(90deg,#e0461d,#e5552a 50%,#dd401a);color:#fff;text-align:center}
.welcome h2{margin-top:40px;font-size:36px}
.welcome p{margin:22px auto 0;width:780px;font-size:15px;line-height:25px}

/* compare */
.section-title{width:100%;text-align:center;font-size:36px}
.rates{top:1068px;left:112px;display:grid;grid-template-columns:repeat(4,232px);column-gap:16px;row-gap:22px}
.rate-card{height:175px;background:#fff;box-shadow:0 2px 10px rgba(0,0,0,.1);display:flex;flex-direction:column;align-items:center;justify-content:flex-end;padding-bottom:20px;text-align:center;font-size:15px;font-weight:700;text-transform:uppercase;line-height:21px}
.rate-card .icon{width:70px;height:70px;border-radius:50%;background:#fbe3dc;margin-bottom:auto;margin-top:30px}
.rate-card.active{background:linear-gradient(135deg,#e8552a,#c42f0c);color:#fff}
.rate-card.active .icon{background:rgba(255,255,255,.25)}

/* who */
.who{top:1770px;left:0;width:1200px;height:433px;background:var(--dark);color:#fff}
.who h2{position:absolute;left:112px;top:75px;font-size:36px}
.who p{position:absolute;left:112px;width:525px;font-size:13.5px;line-height:25px;color:#e6e6e6}
.who .btn{left:112px;top:303px;width:183px;height:47px;background:var(--orange);color:#fff;gap:8px}
.who-ring{left:722px;top:37px;width:365px;height:360px;border-radius:50%;background:var(--orange)}
.who-photo{left:717px;top:37px;width:357px;height:357px;border-radius:50%;background:radial-gradient(circle at 45% 40%,#b89a7a,#6b6f72 60%,#4a4f52)}

/* why */
.why-sub{top:2363px;width:100%;text-align:center;font-size:14px;font-weight:500}
.feature-title{font-size:15px;font-weight:700;text-transform:uppercase;line-height:22px}
.feature-text{font-size:13.5px;line-height:22px;color:var(--body)}
.feat-icon{width:74px;height:74px;border-radius:50%;border:2px solid var(--orange);background:#fff;display:flex;align-items:center;justify-content:center}
.feat-icon i{width:44px;height:44px;border-radius:50%;background:var(--orange);display:block}

/* testimonials */
.clients{top:2917px;left:0;width:1200px;height:480px;background:var(--light)}
.t-card{top:150px;width:308px;height:191px;background:#fff;border-top:3px solid var(--orange);border-radius:14px 14px 8px 8px;text-align:center;padding:60px 24px 0;font-size:13.5px;line-height:26px;color:#444}
.t-avatar{top:104px;width:90px;height:90px;border-radius:50%;border:3px solid #fff;background:linear-gradient(#9a9a9a,#5d5d5d)}
.t-name{top:367px;width:308px;text-align:center;font-size:14px;font-weight:700}
.t-name small{font-size:9px;font-weight:400;color:#666}
.t-stars{top:390px;width:308px;text-align:center;color:#f5c300;font-size:12px;letter-spacing:1px}

/* contact */
.contact{top:3397px;left:0;width:1200px;height:573px;background:linear-gradient(160deg,#e3461d,#d83b15 50%,#e34a20)}
.contact h2{position:absolute;top:55px;width:100%;text-align:center;color:#fff;font-size:36px}
.field{background:#fff;font-size:13px;color:#666;padding:22px 22px}
.submit{left:513px;top:455px;width:174px;height:48px;background:#fff;color:var(--orange);font-size:17px}

/* footer */
.f-item{top:4037px;width:300px;text-align:center}
.f-icon{width:76px;height:76px;margin:0 auto;border-radius:50%;border:2px solid #333;display:flex;align-items:center;justify-content:center}
.f-icon.filled{background:var(--orange);border-color:var(--orange)}
.f-label{margin-top:24px;font-size:15px;font-weight:700}
.f-value{margin-top:10px;font-size:13px;color:#444}
.socials{display:flex;justify-content:center;gap:10px;margin-top:10px}
.socials i{width:16px;height:16px;border-radius:50%;background:#333;display:block}
.footer-rule{top:4213px;left:112px;width:976px;height:1px;background:#ddd}
.copyright{top:4248px;width:100%;text-align:center;font-size:13.5px;color:#555}
.chat{left:1130px;top:4174px;width:38px;height:38px;border-radius:50%;background:var(--orange)}
</style>
</head>
<body>

<header class="site-header abs">
  <div class="logo abs">LENDQUAY</div>
  <svg class="abs" style="left:605px;top:24px" width="26" height="26" viewBox="0 0 24 24" fill="none" stroke="#333" stroke-width="1.5"><path d="M5 3h4l2 5-2.5 1.5a11 11 0 005 5L15 12l5 2v4a2 2 0 01-2 2A16 16 0 013 5a2 2 0 012-2z"/></svg>
  <div class="abs" style="left:642px;top:20px;width:1px;height:36px;background:#bbb"></div>
  <div class="call-label abs">CALL US</div>
  <div class="call-number abs">800 555 0142</div>
  <div class="btn-login pill abs">Log in</div>
  <div class="btn-signup pill abs">Sign up for free</div>
  <nav class="nav abs">
    <span class="active">HOME</span><span>ABOUT US</span><span>SERVICES</span><span>HOW DOES IT WORK?</span><span>CAREERS</span><span>CONTACT US</span><span>● EN ▾</span>
  </nav>
</header>

<section class="hero abs" role="img" aria-label="Photo of a city skyline at dusk seen from a grassy hill">
  <h1 class="hero-title heading abs"><span class="accent">NO</span> OBLIGATIONS<br><span class="accent">NO</span> FEES<br><span class="accent">NO</span> WORRIES</h1>
  <div class="hero-btn pill abs">Find and compare rates <svg width="14" height="14" viewBox="0 0 14 14"><circle cx="7" cy="7" r="7" fill="#fff"/><path d="M5.5 4l3 3-3 3" stroke="#e8431c" stroke-width="1.8" fill="none"/></svg></div>
  <div class="hero-arrow abs" style="left:31px"><svg width="14" height="14"><path d="M9 2L4 7l5 5" stroke="#fff" stroke-width="2" fill="none"/></svg></div>
  <div class="hero-arrow abs" style="left:1127px"><svg width="14" height="14"><path d="M5 2l5 5-5 5" stroke="#fff" stroke-width="2" fill="none"/></svg></div>
</section>

<section class="welcome abs">
  <h2 class="heading">Welcome to Lendquay</h2>
  <p>Lendquay is an online marketplace where you can quickly find &amp; compare great rates from leading mortgage, insurance and finance providers.</p>
</section>

<h2 class="section-title heading abs" style="top:987px">Find and <span class="accent">compare rates</span></h2>
<div class="rates abs">
  <div class="rate-card"><span class="icon" role="img" aria-label="Line icon of a house over a hand"></span>Mortgage rates</div>
  <div class="rate-card"><span class="icon" role="img" aria-label="Line icon of a person with documents"></span>Personal finance</div>
  <div class="rate-card"><span class="icon" role="img" aria-label="Line icon of a car and a coin"></span>Vehicle finance</div>
  <div class="rate-card"><span class="icon" role="img" aria-label="Line icon of buildings over a hand"></span>Business &amp; asset<br>finance</div>
  <div class="rate-card"><span class="icon" role="img" aria-label="Line icon of a person at an office building"></span>Commercial finance</div>
  <div class="rate-card active"><span class="icon" role="img" aria-label="Line icon of a money bag in hands"></span>Insurance rates</div>
  <div class="rate-card"><span class="icon" role="img" aria-label="Line icon of a car over a hand"></span>Vehicle leasing</div>
  <div class="rate-card"><span class="icon" role="img" aria-label="Line icon of a house and car"></span>Home, contents &amp; car</div>
  <div class="rate-card"><span class="icon" role="img" aria-label="Line icon of a barn under an umbrella"></span>Farming &amp; rural<br>insurance</div>
  <div class="rate-card"><span class="icon" role="img" aria-label="Line icon of a power pylon"></span>Power &amp; gas</div>
  <div class="rate-card"><span class="icon" role="img" aria-label="Line icon of a globe"></span>Internet &amp; fibre</div>
  <div class="rate-card"><span class="icon" role="img" aria-label="Line icon of a phone handset"></span>Phone &amp; mobile</div>
</div>

<section class="who abs">
  <h2 class="heading">Who is Lendquay?</h2>
  <p style="top:135px">Lendquay CEO Daniel Hart doesn’t like door knockers. They have a habit of showing up during dinner, or interrupting family time. He decided there must be a better way to field offers from service providers. So now, there is.</p>
  <p style="top:222px">“Our goal is to get major banks, insurance companies, utility companies and other consumer service suppliers fighting for the consumer’s business.”</p>
  <div class="btn pill abs">Learn more <svg width="14" height="14" viewBox="0 0 14 14"><circle cx="7" cy="7" r="7" fill="#fff"/><path d="M5.5 4l3 3-3 3" stroke="#e8431c" stroke-width="1.8" fill="none"/></svg></div>
  <div class="who-ring abs"></div>
  <div class="who-photo abs" role="img" aria-label="Photo of three friends looking at a tablet at an outdoor table"></div>
</section>

<h2 class="section-title heading abs" style="top:2312px">Why <span class="accent">Lendquay?</span></h2>
<p class="why-sub abs">Our mission is to put the power in the hands of the consumer</p>
<svg class="abs" style="left:400px;top:2425px" width="400" height="400" viewBox="0 0 400 400">
  <circle cx="200" cy="200" r="180" fill="none" stroke="#666" stroke-width="1.5" stroke-dasharray="6 6"/>
  <circle cx="200" cy="200" r="147" fill="#fff" stroke="#f0f0f0" stroke-width="6"/>
  <circle cx="62" cy="84" r="8" fill="#e8431c"/><circle cx="337" cy="84" r="8" fill="#e8431c"/>
  <circle cx="52" cy="303" r="8" fill="#e8431c"/><circle cx="348" cy="303" r="8" fill="#e8431c"/>
  <text x="200" y="219" text-anchor="middle" font-family="Rajdhani,sans-serif" font-weight="500" font-size="54" fill="#e8431c">LENDQUAY</text>
</svg>

<div class="feature-title abs" style="left:157px;top:2448px;width:180px;text-align:right">Great rates &amp;<br>incentives</div>
<div class="feat-icon abs" style="left:348px;top:2433px"><i></i></div>
<p class="feature-text abs" style="left:135px;top:2521px;width:270px;text-align:right">Receive the great rates and incentives hassle-free Lendquay does the shopping around for you.</p>

<div class="feature-title abs" style="left:108px;top:2667px;width:215px;text-align:right">Any time. Any where</div>
<div class="feat-icon abs" style="left:328px;top:2641px"><i></i></div>
<p class="feature-text abs" style="left:108px;top:2729px;width:277px;text-align:right">Get notifications and review representative offers wherever you are with your personal, mobile-friendly Lendquay dashboard.</p>

<div class="feat-icon abs" style="left:778px;top:2433px"><i></i></div>
<div class="feature-title abs" style="left:870px;top:2459px;width:220px">Privacy is important</div>
<p class="feature-text abs" style="left:803px;top:2521px;width:290px">Your private information is disclosed only when you follow up on representative offers from a service provider.</p>

<div class="feat-icon abs" style="left:803px;top:2641px"><i></i></div>
<div class="feature-title abs" style="left:897px;top:2656px;width:200px">No fees, no<br>obligations</div>
<p class="feature-text abs" style="left:810px;top:2729px;width:280px">The Lendquay service is free and you are under no obligation until you select the representative offer that best suits your needs.</p>

<section class="clients abs">
  <h2 class="section-title heading abs" style="top:38px">What our <span class="accent">clients say?</span></h2>
  <div class="t-card abs" style="left:112px">“What an awesome experience, Lendquay was quick simple and easy to follow. It was great to have someone do all the hard work for me.</div>
  <div class="t-card abs" style="left:445px">“I have been with my bank for the past 25 years and I rang them for a mortgage rate and they offered me 4.35%. I then heard about Lendquay and thought I</div>
  <div class="t-card abs" style="left:778px">“I called Lendquay and they went out of their way to help me and had me pre-approved in a day.”</div>
  <div class="t-avatar abs" style="left:221px" role="img" aria-label="Portrait photo of a client"></div>
  <div class="t-avatar abs" style="left:554px" role="img" aria-label="Portrait photo of a client"></div>
  <div class="t-avatar abs" style="left:887px" role="img" aria-label="Portrait photo of a client"></div>
  <div class="t-name abs" style="left:112px">Tom, <small>Chairman NKL</small></div>
  <div class="t-name abs" style="left:445px">Auckland, <small>Project Manager</small></div>
  <div class="t-name abs" style="left:778px">Owen, <small>Chairman NKL</small></div>
  <div class="t-stars abs" style="left:112px">★★★★★</div>
  <div class="t-stars abs" style="left:445px">★★★★★</div>
  <div class="t-stars abs" style="left:778px">★★★★★</div>
</section>

<section class="contact abs">
  <h2 class="heading">Contact us</h2>
  <div class="field abs" style="left:177px;top:136px;width:413px;height:54px">First Name</div>
  <div class="field abs" style="left:610px;top:136px;width:413px;height:54px">Last Name</div>
  <div class="field abs" style="left:177px;top:208px;width:413px;height:54px">Email</div>
  <div class="field abs" style="left:610px;top:208px;width:413px;height:54px">Phone</div>
  <div class="field abs" style="left:177px;top:281px;width:846px;height:125px">Message</div>
  <div class="submit pill abs">Submit</div>
</section>

<div class="f-item abs" style="left:57px">
  <div class="f-icon"><svg width="28" height="28" viewBox="0 0 24 24"><path d="M5 3h4l2 5-2.5 1.5a11 11 0 005 5L15 12l5 2v4a2 2 0 01-2 2A16 16 0 013 5a2 2 0 012-2z" fill="#333"/></svg></div>
  <div class="f-label">PHONE</div><div class="f-value">0508 55 01 42</div>
</div>
<div class="f-item abs" style="left:312px">
  <div class="f-icon filled"><svg width="26" height="30" viewBox="0 0 24 28"><path d="M12 1a9 9 0 00-9 9c0 7 9 17 9 17s9-10 9-17a9 9 0 00-9-9z" fill="#fff"/><circle cx="12" cy="10" r="3.5" fill="#e8431c"/></svg></div>
  <div class="f-label">MAIN OFFICE</div><div class="f-value">14 Harbour Lane, Auckland 1010, New Zealand</div>
</div>
<div class="f-item abs" style="left:578px">
  <div class="f-icon"><svg width="30" height="22" viewBox="0 0 30 22"><rect x="1" y="1" width="28" height="20" rx="2" fill="#333"/><path d="M2 3l13 10L28 3" stroke="#fff" stroke-width="2" fill="none"/></svg></div>
  <div class="f-label">EMAIL</div><div class="f-value">info@lendquay.co.nz</div>
</div>
<div class="f-item abs" style="left:830px">
  <div class="f-icon"><svg width="28" height="28"><circle cx="14" cy="14" r="12" fill="#333"/></svg></div>
  <div class="f-label">SOCIAL MEDIA</div>
  <div class="socials"><i></i><i></i><i></i><i></i></div>
</div>
<div class="footer-rule abs"></div>
<p class="copyright abs">© 2020 LENDQUAY. All Rights Reserved &nbsp; | &nbsp; Privacy Policy &nbsp; | &nbsp; Terms &amp; Condition</p>
<div class="chat abs"></div>

</body>
</html>
```